We want to design total new business card and logo for Kestrel Building Services Ltd

Our company name Kestrel Building Services Ltd. Design new logo and business card , need hi-end luxury style art for architecture and construction industry. The card should simple but stylish. Our business focus on CONNECT tradesman to construction company, help marketing construction company tender oversea projects, managing franchise in construction sector, delivery amazing services to our client, so Logo should show the CONNECTION IDEA, CONNECTING PEOPLE, LUXURY. Visit our website for more information: kestrelgroup.example.nz

Target Market(s)

Directors or managers

Industry/Entity Type

Construction Company

Contact Information for Business Card

Name, Title, Mobile, Email, Website

Font styles to use
Serif

Colors

Designer to choose colors to be used in the design.

Requirements
Must have
• Simple and luxury, connection icon
Nice to have
• Special materials, plastic card, look through,...
• Look new ideas.

```html
<!DOCTYPE html>
<html lang="en">
<head>
<meta charset="utf-8">
<title>Kestrel Building Services – Business Card</title>
<link rel="stylesheet" href="https://fonts.googleapis.com/css2?family=Cormorant+Garamond:wght@500;600;700&display=swap">
<style>
  :root {
    --backdrop: #161616;
    --card: #1c1c1e;
    --card-edge: #2a2a2d;
    --accent: #1ea7cc;
    --silver: #d9d9d9;
    --text: #f2f2f2;
    --rule: #45454a;
  }
  * { box-sizing: border-box; margin: 0; padding: 0; }
  html, body { width: 1200px; height: 900px; overflow: hidden; background: var(--backdrop); }
  body { font-family: "Cormorant Garamond", Georgia, serif; font-weight: 600; color: var(--text); position: relative; }

  .card {
    position: absolute;
    width: 600px; height: 340px;
    background: var(--card);
    border: 1px solid var(--card-edge);
    border-radius: 24px;
    box-shadow: 0 18px 40px rgba(0,0,0,.6);
  }

  /* back side */
  .card-back { left: 110px; top: 90px; }
  .card-back .brand-lockup {
    position: absolute; left: 0; right: 0; top: 100px;
    display: flex; justify-content: center; align-items: center; gap: 18px;
  }
  .card-back .connect-mark {
    width: 40px; height: 40px; border-radius: 50%;
    border: 3px solid var(--silver);
  }
  .card-back .brand-mark {
    font-weight: 700; font-size: 50px; letter-spacing: 8px;
    color: var(--silver);
  }
  .card-back .tagline {
    position: absolute; left: 0; right: 0; bottom: 56px;
    text-align: center;
    font-size: 17px; letter-spacing: 1.5px; color: var(--text);
  }

  /* front side */
  .card-front { left: 490px; top: 470px; }
  .brand-lockup-front {
    position: absolute; right: 34px; top: 40px;
    display: flex; align-items: center; gap: 12px;
  }
  .brand-lockup-front .connect-mark {
    width: 24px; height: 24px; border-radius: 50%;
    border: 3px solid var(--accent);
  }
  .brand-name {
    font-weight: 700; font-size: 27px; letter-spacing: .5px;
    color: var(--accent);
  }
  .social {
    position: absolute; right: 34px; top: 98px;
    display: flex; gap: 6px;
  }
  .social span { width: 18px; height: 18px; border-radius: 50%; background: var(--text); }
  .rule-top {
    position: absolute; right: 134px; top: 107px; width: 200px; height: 1px;
    background: linear-gradient(90deg, transparent, var(--rule));
  }
  .rule-mid {
    position: absolute; left: 205px; top: 176px; width: 165px; height: 1px;
    background: linear-gradient(90deg, var(--rule), transparent);
  }

  .person { position: absolute; left: 40px; top: 158px; }
  .person .name { font-weight: 700; font-size: 25px; color: var(--accent); line-height: 1.1; }
  .person .role { font-size: 18px; margin-bottom: 8px; }
  .contact-list { list-style: none; font-size: 18px; line-height: 1.35; }
  .contact-list li { display: flex; align-items: center; gap: 10px; }
  .contact-list svg { width: 14px; height: 14px; fill: var(--accent); flex: none; }

  .company { position: absolute; right: 34px; top: 172px; text-align: right; font-size: 17px; line-height: 1.35; font-style: normal; }
  .company .legal-name { color: var(--accent); }
</style>
</head>
<body>
  <section class="card card-back" aria-label="Card back">
    <div class="brand-lockup">
      <span class="connect-mark" aria-hidden="true"></span>
      <div class="brand-mark">KESTREL</div>
    </div>
    <p class="tagline">AMAZING SERVICES AFFORDABLE PRICE</p>
  </section>

  <section class="card card-front" aria-label="Card front">
    <div class="brand-lockup-front">
      <span class="connect-mark" aria-hidden="true"></span>
      <div class="brand-name">KESTREL BUILDING SERVICES</div>
    </div>
    <div class="rule-top"></div>
    <div class="social" aria-label="Social links"><span></span><span></span><span></span><span></span></div>
    <div class="rule-mid"></div>

    <div class="person">
      <p class="name">MARCUS HALE</p>
      <p class="role">Managing Director</p>
      <ul class="contact-list">
        <li><svg viewBox="0 0 16 16" aria-hidden="true"><path d="M3 1h3l1 4-2 1a9 9 0 0 0 5 5l1-2 4 1v3a2 2 0 0 1-2 2A13 13 0 0 1 1 3a2 2 0 0 1 2-2z"/></svg>0800 555 014</li>
        <li><svg viewBox="0 0 16 16" aria-hidden="true"><path d="M3 1h3l1 4-2 1a9 9 0 0 0 5 5l1-2 4 1v3a2 2 0 0 1-2 2A13 13 0 0 1 1 3a2 2 0 0 1 2-2z"/></svg>021 555 0192</li>
        <li><svg viewBox="0 0 16 16" aria-hidden="true"><path d="M1 3h14v10H1z M1 3l7 6 7-6" fill="none" stroke="#1ea7cc" stroke-width="1.6"/></svg>info@kestrelgroup.example.nz</li>
        <li><svg viewBox="0 0 16 16" aria-hidden="true"><circle cx="8" cy="8" r="7"/></svg>www.kestrelgroup.example.nz</li>
      </ul>
    </div>

    <address class="company">
      <p class="legal-name">KESTREL BUILDING SERVICES LTD</p>
      <p>18 Harbour Lane, Westmere</p>
      <p>Auckland 1022, New Zealand</p>
    </address>
  </section>
</body>
</html>
```